Automotive eCommerce Business looking for a business card design

Looking for a clean and simple business card design. Our company name is "Brindle Auto" and we are a company specializing in the ecommerce sales of automotive parts, specifically for pick up trucks and large SUVs. Our company colours are red, black, and white.

Feel free to use the logo provided or create a new logo that you seem fit. Looking forward to your creative ideas!

Industry/Entity Type

Automotive

Contact Information for Business Card

We were thinking of a possibly two-sided design featuring just the logo and company name on one side, and personal information on the other side. Single sided designs will be considered as well.

Font styles to use
Serif
Sans Serif
Decorative

Colors
ec1f27
ffffff
000000

Requirements
Must have
• Space for employee's name, title, phone number and email address, along with the company address and website somewhere.

```html
<!DOCTYPE html>
<html lang="en">
<head>
<meta charset="utf-8">
<title>Brindle Auto Ltd – Business Card</title>
<link rel="stylesheet" href="https://fonts.googleapis.com/css2?family=Raleway:wght@700&family=Source+Sans+3:wght@400;600;700&display=swap">
<style>
  :root {
    --stage: #1b1b1b;
    --card-light: #f2f2f2;
    --brand-red: #a11d22;
    --brand-red-light: #b0353a;
    --ink: #111111;
    --white: #ffffff;
  }
  * { margin: 0; padding: 0; box-sizing: border-box; }
  html, body {
    width: 1200px;
    height: 900px;
    overflow: hidden;
    background: var(--stage);
  }
  .canvas {
    position: relative;
    width: 1200px;
    height: 900px;
  }
  .card {
    position: absolute;
    top: 170px;
    width: 347px;
    height: 561px;
  }
  .card-front {
    left: 259px;
    background: var(--card-light);
    font-family: "Source Sans 3", sans-serif;
    color: var(--ink);
    text-align: center;
  }
  .brand-square {
    position: absolute;
    left: 123px;
    top: 84px;
    width: 100px;
    height: 100px;
    background: var(--brand-red);
  }
  .company-name {
    position: absolute;
    left: 0;
    right: 0;
    top: 224px;
    font-family: "Raleway", sans-serif;
    font-weight: 700;
    font-size: 35px;
    letter-spacing: -0.3px;
    color: var(--ink);
  }
  .person {
    position: absolute;
    left: 0;
    right: 0;
    top: 338px;
  }
  .person-name {
    font-weight: 700;
    font-size: 22px;
    color: var(--brand-red);
    line-height: 26px;
  }
  .person-title {
    font-size: 15px;
    line-height: 22px;
  }
  .contact {
    position: absolute;
    left: 0;
    right: 0;
    top: 402px;
    font-size: 15px;
    line-height: 21px;
  }
  .contact .label {
    color: var(--brand-red);
    font-weight: 700;
  }
  .contact .website {
    color: var(--brand-red);
    font-weight: 700;
  }
  .address {
    position: absolute;
    left: 0;
    right: 0;
    top: 480px;
    font-size: 15px;
    line-height: 17px;
  }
  .card-back {
    left: 631px;
    background: radial-gradient(circle at 50% 45%, var(--brand-red-light) 0%, var(--brand-red) 75%);
    display: flex;
    align-items: center;
    justify-content: center;
  }
  .back-name {
    font-family: "Raleway", sans-serif;
    font-weight: 700;
    font-size: 34px;
    color: var(--white);
  }
</style>
</head>
<body>
<main class="canvas">
  <section class="card card-front">
    <div class="brand-square" aria-hidden="true"></div>
    <h1 class="company-name">Brindle Auto Ltd</h1>
    <div class="person">
      <p class="person-name">MARA ELLISON</p>
      <p class="person-title">Managing Director</p>
    </div>
    <div class="contact">
      <p><span class="label">P:</span> 555-310-2468</p>
      <p><span class="label">E:</span> info@youremail.com</p>
      <p class="website">www.websitename.com</p>
    </div>
    <div class="address">
      <p>1234, Address Goes Here</p>
      <p>Country Name, 123456</p>
    </div>
  </section>
  <section class="card card-back">
    <p class="back-name">Brindle Auto</p>
  </section>
</main>
</body>
</html>
```